Building company buisness cards

We are looking for a sharp modern new look for our business cards.
We are a New Zealand based company that specialises in house and land packages.
We have attached a photo of the current logo and would like to see if it can be improved somehow if needed.
We are open to any colours but we have chosen green at this stage.
Feel free to change the font and make the logo smarter looking.
Play with the colours and see what looks best.

We want a card that looks so good know one will want to throw it away!

Target Market(s)

Home buyers

Industry/Entity Type

Building

Contact Information for Business Card

Derek Tolvane
0217394062
dtolvane@quillmarkhomesteads.co.nz
quillmarkhomesteads.co.nz

Font styles to use
Serif
Sans Serif

Colors

Designer to choose colors to be used in the design.

Requirements
Must have
• Logo and company name on one side, details on the other side
Nice to have
• Color codes for the original green are HEX #4a8028, RGB(74,128,40), CMYK(42,0,69,50)
• Round corners, Raised and/or spot UV

```html
<!DOCTYPE html>
<html lang="en">
<head>
<meta charset="utf-8">
<title>Quillmark Homesteads – Business Cards</title>
<link rel="stylesheet" href="https://fonts.googleapis.com/css2?family=Open+Sans:wght@400;800&display=swap">
<style>
  :root {
    --brand-green: #2a9a22;
    --paper: #ffffff;
    --ink: #1c1c1c;
    --rule: #3a3a3a;
    --backdrop: #e6e7e6;
  }
  * { box-sizing: border-box; margin: 0; padding: 0; }
  html, body {
    width: 1200px;
    height: 716px;
    overflow: hidden;
    background: var(--backdrop);
    font-family: "Open Sans", sans-serif;
  }
  .sheet {
    position: relative;
    width: 1200px;
    height: 716px;
    display: flex;
    justify-content: center;
    align-items: center;
    gap: 60px;
  }
  .card {
    position: relative;
    width: 510px;
    height: 292px;
    border-radius: 6px;
    box-shadow: 0 6px 18px rgba(0,0,0,0.18);
    overflow: hidden;
  }
  .card--front {
    background: var(--brand-green);
    display: flex;
    flex-direction: column;
    align-items: center;
    justify-content: center;
  }
  .wordmark {
    font-weight: 800;
    line-height: 0.95;
    text-align: center;
    letter-spacing: -0.5px;
  }
  .wordmark__top { display: block; font-size: 22px; }
  .wordmark__bottom { display: block; font-size: 34px; }
  .card--front .wordmark { color: var(--paper); }
  .wordmark-mark {
    width: 12px;
    height: 12px;
    margin-bottom: 8px;
  }
  .card--front .wordmark-mark { background: var(--paper); }
  .underline {
    width: 56px;
    height: 1px;
    margin-top: 10px;
    background: rgba(255,255,255,0.6);
  }

  .card--back { background: var(--paper); }
  .card--back .brand {
    position: absolute;
    top: 44px;
    left: 0;
    width: 100%;
    display: flex;
    flex-direction: column;
    align-items: center;
  }
  .card--back .wordmark { color: var(--brand-green); }
  .card--back .wordmark-mark { background: var(--brand-green); }
  .card--back .underline { background: #b9d9b5; }

  .name-row {
    position: absolute;
    left: 28px;
    right: 30px;
    top: 154px;
    display: flex;
    align-items: center;
    gap: 12px;
  }
  .name-rule {
    flex: 1 1 auto;
    height: 1px;
    margin-top: 4px;
    background: var(--rule);
  }
  .person-name {
    flex: 0 0 auto;
    font-size: 21px;
    font-weight: 400;
    line-height: 1.2;
    color: var(--brand-green);
    white-space: nowrap;
  }

  .contacts {
    position: absolute;
    right: 30px;
    top: 205px;
    list-style: none;
    display: flex;
    flex-direction: column;
    align-items: flex-end;
    gap: 4px;
  }
  .contacts li {
    display: flex;
    align-items: center;
    gap: 10px;
    font-size: 13px;
    line-height: 18px;
    color: var(--ink);
    white-space: nowrap;
  }
  .contacts__icon {
    width: 15px;
    height: 15px;
    background: var(--brand-green);
    border-radius: 2px;
    display: flex;
    align-items: center;
    justify-content: center;
  }
  .contacts__icon svg { width: 11px; height: 11px; }
</style>
</head>
<body>
<main class="sheet">
  <section class="card card--front" aria-label="Card front">
    <div class="wordmark-mark"></div>
    <div class="wordmark">
      <span class="wordmark__top">quillmark</span>
      <span class="wordmark__bottom">homesteads.</span>
    </div>
    <div class="underline"></div>
  </section>

  <section class="card card--back" aria-label="Card back">
    <div class="brand">
      <div class="wordmark-mark"></div>
      <div class="wordmark">
        <span class="wordmark__top">quillmark</span>
        <span class="wordmark__bottom">homesteads.</span>
      </div>
      <div class="underline"></div>
    </div>

    <div class="name-row">
      <div class="name-rule"></div>
      <p class="person-name">Derek Tolvane</p>
    </div>

    <ul class="contacts">
      <li>
        <span class="contacts__text">0217394062</span>
        <span class="contacts__icon">
          <svg viewBox="0 0 12 12" aria-hidden="true"><path d="M3 1.5 L4.6 1.5 L5.2 4 L4.1 4.8 Q5 6.9 7.2 7.9 L8 6.8 L10.5 7.4 L10.5 9 Q10.5 10.5 9 10.5 Q2 10 1.5 3 Q1.5 1.5 3 1.5Z" fill="#fff"/></svg>
        </span>
      </li>
      <li>
        <span class="contacts__text">dtolvane@quillmarkhomesteads.co.nz</span>
        <span class="contacts__icon">
          <svg viewBox="0 0 12 12" aria-hidden="true"><rect x="1.5" y="3" width="9" height="6.5" fill="none" stroke="#fff" stroke-width="1.1"/><path d="M1.5 3 L6 6.8 L10.5 3" fill="none" stroke="#fff" stroke-width="1.1"/></svg>
        </span>
      </li>
      <li>
        <span class="contacts__text">quillmarkhomesteads.co.nz</span>
        <span class="contacts__icon">
          <svg viewBox="0 0 12 12" aria-hidden="true"><circle cx="6" cy="6" r="4.5" fill="none" stroke="#fff" stroke-width="1.1"/><ellipse cx="6" cy="6" rx="2" ry="4.5" fill="none" stroke="#fff" stroke-width="0.9"/><line x1="1.5" y1="6" x2="10.5" y2="6" stroke="#fff" stroke-width="0.9"/></svg>
        </span>
      </li>
    </ul>
  </section>
</main>
</body>
</html>
```